Create the ONLY Supplement line for Male Entrepreneurs! (Verity Nine MD)

I need a label designed for a new supplement brand that I am launching.

There are five products so need a design that I can simply change the wording for each individual product

The brand name is called verity nine MD. The focus is male entrepreneurial health.

Target audience is men 35 to 55.

Concepts: the healthier you are in body the more money you will make in business.

Concept to copy: I want to make a clean minimalistic label mimicking Lansworth MD (google it and you'll see what I mean)

Target Market(s)

male entrepreneurs 35-55

Industry/Entity Type

Health Supplement

Colors

Designer to choose colors to be used in the design.

Requirements
Must have
• Modern classy design, similar to Lansworth MD.
Nice to have
• Highlight that the supplement is Doctor Approved.
Should not have
• No loud colors. Present it as high class.

```html
<!DOCTYPE html>
<html lang="en">
<head>
<meta charset="utf-8">
<title>Verity Nine MD – Omega-3 Label</title>
<link rel="stylesheet" href="https://fonts.googleapis.com/css2?family=Lora:wght@400;600;700&family=Montserrat:wght@300;400;600&family=Roboto:wght@400;700;900&display=swap">
<style>
  :root {
    --wine: #7a2a2a;
    --wine-deep: #5c1a14;
    --ink: #222222;
    --text: #3a3a3a;
    --label: #f4f3f2;
    --stage: #ece7e4;
    --rule-grey: #bdbdbd;
    --pill: #d6d6d6;
  }
  * { box-sizing: border-box; margin: 0; padding: 0; }
  html, body { width: 1200px; height: 722px; overflow: hidden; }
  body { background: var(--stage); font-family: 'Montserrat', sans-serif; color: var(--text); }
  .label-set { position: relative; width: 1200px; height: 722px; }
  .panel {
    position: absolute; top: 150px; width: 360px; height: 420px;
    background: var(--label);
    box-shadow: 0 4px 18px rgba(60, 20, 15, 0.15);
  }
  .panel--directions { left: 50px; }
  .panel--front { left: 420px; }
  .panel--facts { left: 790px; }

  /* Directions panel */
  .directions { position: absolute; left: 60px; top: 22px; width: 240px; }
  .directions h2 {
    font-family: 'Lora', serif; font-weight: 600; color: var(--wine);
    font-size: 14px; letter-spacing: .5px; text-align: center; margin-bottom: 8px;
  }
  .directions .body {
    font-weight: 300; font-size: 10.6px; line-height: 13.4px; text-align: justify;
  }
  .rule { border: 0; border-top: 1px solid var(--wine); margin: 12px 0; }
  .fda {
    font-weight: 600; font-size: 10.4px; line-height: 13.6px; text-align: center; color: var(--ink);
  }
  .notes { font-weight: 300; font-size: 10.2px; line-height: 12.8px; }
  .notes strong { font-weight: 600; color: var(--ink); }
  .footer-line {
    position: absolute; left: 0; right: 0; bottom: 22px; text-align: center;
    font-family: 'Lora', serif; font-size: 15.5px; color: var(--ink);
  }
  .footer-line span { margin: 0 8px; }

  /* Front panel */
  .brand { position: absolute; top: 28px; left: 0; right: 0; text-align: center; }
  .brand-name { font-family: 'Lora', serif; font-weight: 400; font-size: 32px; color: var(--wine); line-height: 38px; }
  .brand-tag { font-weight: 400; font-size: 13.5px; color: #444; margin-top: 4px; }
  .hero-icon { position: absolute; left: 148px; top: 160px; width: 84px; height: 46px; border-radius: 24px; background: #d9cfcf; }
  .category {
    position: absolute; top: 222px; left: 62px; right: 62px; height: 18px;
    border-top: 1px solid var(--rule-grey); margin-top: 8px;
  }
  .category span {
    position: absolute; left: 50%; top: -9px; transform: translateX(-50%);
    background: var(--pill); border-radius: 9px; padding: 0 18px; height: 18px;
    font-size: 14px; line-height: 18px; color: #333; white-space: nowrap;
  }
  .product-name {
    position: absolute; top: 242px; left: 0; right: 0; text-align: center;
    font-family: 'Lora', serif; font-weight: 700; font-size: 46px; color: var(--wine); letter-spacing: 1px;
  }
  .front-rule { position: absolute; left: 62px; right: 62px; border-top: 1px solid var(--wine); }
  .front-rule--a { top: 304px; }
  .front-rule--b { top: 352px; }
  .slogan {
    position: absolute; top: 310px; left: 60px; right: 60px; text-align: center;
    font-weight: 300; font-size: 11.4px; line-height: 14.5px; color: #333;
  }

  /* Facts panel */
  .facts {
    position: absolute; left: 72px; top: 22px; width: 208px;
    border: 1px solid #555; padding: 6px 7px 4px; font-family: 'Roboto', sans-serif; color: var(--ink);
  }
  .facts h3 { font-weight: 900; font-size: 21px; color: var(--wine-deep); line-height: 24px; padding-left: 10px; }
  .facts .row { display: flex; justify-content: space-between; font-size: 8.6px; line-height: 13.6px; padding: 0 12px; border-top: 1px solid #999; }
  .facts .row.plain { border-top: 0; line-height: 11px; }
  .facts .row.indent { padding-left: 25px; }
  .facts .bold { font-weight: 700; }
  .facts .bar { height: 5px; background: #222; margin: 2px 0; }
  .facts .dv { text-align: right; font-size: 6px; font-weight: 700; padding: 2px 12px 1px; }
  .facts .note { font-size: 6.2px; line-height: 8px; padding: 3px 12px 3px; }
  .badges { position: absolute; left: 72px; top: 318px; width: 208px; display: flex; justify-content: space-between; }
  .badge { width: 46px; text-align: center; font-family: 'Roboto', sans-serif; font-weight: 700; font-size: 7px; color: #333; }
  .badge svg { display: block; margin: 0 auto 4px; }
</style>
</head>
<body>
<main class="label-set">

  <section class="panel panel--directions">
    <div class="directions">
      <h2>DIRECTIONS</h2>
      <p class="body">Take two capsules twice per day or as directed by your healthcare practitioner. Prime Vigor is our powerful blend of eight synergistic ingredients designed to help support healthy testosterone levels in men.* Additionally, the select ingredients in this formula have been proven clinically effective in supporting sexual health and energy, promoting healthy cortisol levels and providing dopamine support.*</p>
      <hr class="rule">
      <p class="fda">*These statements have not been evaluated by the Food and Drug Administration. This product is not intended to diagnose, treat, cure or prevent any disease.</p>
      <hr class="rule">
      <p class="notes"><strong>Caution:</strong> Keep out of reach of children.<br>
      <strong>Storage:</strong> Keep tightly closed in a cool, dry place.<br>
      <strong>Does Not Contain:</strong> Milk, eggs, fish, shellfish, tree nuts, peanuts, wheat, soy. To report a serious adverse event, call: 555.010.0199</p>
    </div>
    <p class="footer-line">Dietary Supplement<span>|</span>90 Softgels</p>
  </section>

  <section class="panel panel--front">
    <div class="brand">
      <div class="brand-name">Verity Nine MD</div>
      <div class="brand-tag">Male Entrepreneurial Health</div>
    </div>
    <div class="hero-icon" role="img" aria-label="Line icon of a fish with oil drops"></div>
    <div class="category"><span>Nutriceuticals</span></div>
    <h1 class="product-name">OMEGA-3</h1>
    <div class="front-rule front-rule--a"></div>
    <p class="slogan">The healthier you are in body the more money you will make in business</p>
    <div class="front-rule front-rule--b"></div>
    <p class="footer-line">Dietary Supplement<span>|</span>90 Softgels</p>
  </section>

  <section class="panel panel--facts">
    <div class="facts">
      <h3>Nutrition Facts</h3>
      <div class="row plain"><span>Serving Size</span><span>...g</span></div>
      <div class="row plain"><span>Servings Per Container</span><span></span></div>
      <div class="bar"></div>
      <div class="row plain bold"><span>Amount Per Serving</span></div>
      <div class="row"><span><b>Calories</b> ....</span><span>Calories from Fat ...</span></div>
      <div class="bar" style="height:3px"></div>
      <div class="dv">% Daily Value*</div>
      <div class="row"><span><b>Total Fat</b> ...g</span><b>...%</b></div>
      <div class="row indent"><span>Saturated Fat ...g</span><b>...%</b></div>
      <div class="row indent"><span><i>Trans</i> Fat ...g</span></div>
      <div class="row"><span><b>Cholestrol</b> ...mg</span><b>...%</b></div>
      <div class="row indent"><span><b>Sodium</b> ...mg</span><b>...%</b></div>
      <div class="row"><span><b>Total Carbohydrate</b> ...g</span><b>...%</b></div>
      <div class="row indent"><span>Dietary Fiber ...g</span><b>...%</b></div>
      <div class="row indent"><span>Sugars ...g</span></div>
      <div class="row"><span><b>Protein</b> ...g</span></div>
      <div class="bar"></div>
      <p class="note">*Percent Daily Values are based on a 2,000 calorie diet. Your Daily Values may be higer or lower depending on your calorie needs.</p>
      <div class="bar" style="height:3px"></div>
    </div>
    <div class="badges">
      <div class="badge"><svg width="38" height="38"><circle cx="19" cy="19" r="17" fill="none" stroke="var(--wine)" stroke-width="2"/></svg>GMO FREE</div>
      <div class="badge"><svg width="38" height="38"><circle cx="19" cy="19" r="17" fill="none" stroke="var(--wine)" stroke-width="2"/></svg>GLUTEN FREE</div>
      <div class="badge"><svg width="38" height="38"><circle cx="19" cy="19" r="17" fill="none" stroke="var(--wine)" stroke-width="2"/></svg>SUGAR FREE</div>
      <div class="badge"><svg width="38" height="38"><circle cx="19" cy="19" r="17" fill="none" stroke="var(--wine)" stroke-width="2"/></svg>LACTOSE FREE</div>
    </div>
  </section>

</main>
</body>
</html>
```